VOR Exterior Coatings

double sided. the front i want the name of the business each word on a new line with the VOR being bigger. id like teal, black and white colors. the back i want my contact info. Flat, no gloss. Something professional and I want to feel the letters bump put of the card. if possible maybe a paint sprayer in corner. not a car paint spray. (no tank on top of gun)
no vehicle paint sprayers. that means no tank on top of the gun. doesn't have to have a sprayer. black/dark background on the front. white back ground on back with info

```html
<!DOCTYPE html>
<html lang="en">
<head>
<meta charset="utf-8">
<title>VOR Exterior Coatings – Business Card</title>
<link rel="stylesheet" href="https://fonts.googleapis.com/css2?family=Lato:wght@400;700;900&display=swap">
<style>
  :root {
    --backdrop: #6a6a6a;
    --card-white: #f6f6f5;
    --teal: #006d6d;
    --teal-deep: #006a6b;
    --cyan-emboss: #22d6dc;
    --ink: #111111;
    --grey-text: #555a5c;
    --divider: #8c8c8c;
  }
  * { box-sizing: border-box; margin: 0; padding: 0; }
  html, body {
    width: 1200px; height: 800px; overflow: hidden;
    background: var(--backdrop);
    font-family: "Lato", Arial, sans-serif;
  }
  .canvas {
    position: relative; width: 1200px; height: 800px;
  }
  .card {
    position: absolute;
    width: 620px; height: 354px;
    border-radius: 3px;
    box-shadow: 0 10px 26px rgba(0,0,0,0.35);
  }
  /* Contact side */
  .card--contact {
    left: 120px; top: 30px;
    background: var(--card-white);
    display: flex; align-items: center;
  }
  .card--contact .brand {
    width: 290px;
    display: flex; flex-direction: column; align-items: center;
    color: var(--teal);
    font-weight: 900;
    line-height: 1;
  }
  .brand__main { font-size: 92px; letter-spacing: 1px; }
  .brand__sub { font-size: 19px; letter-spacing: 1px; margin-top: 6px; text-transform: uppercase; }
  .divider {
    width: 1px; height: 190px; background: var(--divider);
  }
  .contact {
    padding-left: 26px;
    color: var(--grey-text);
    font-size: 13.5px;
    line-height: 1.35;
  }
  .contact__name {
    color: var(--teal); font-weight: 700; font-size: 21px;
    text-transform: uppercase; letter-spacing: 0.5px; line-height: 1.1;
  }
  .contact__title { font-size: 14px; margin-bottom: 10px; }
  .contact__address { margin-bottom: 10px; }
  .contact__list { list-style: none; }
  .contact__list li { display: flex; align-items: center; gap: 8px; }
  .contact__list svg { width: 12px; height: 12px; flex: none; }
  .icon { fill: var(--teal); }

  /* Brand side */
  .card--brand {
    left: 460px; top: 416px;
    background: var(--teal-deep);
    display: flex; align-items: center; justify-content: center;
  }
  .card--brand .brand { width: auto; color: var(--cyan-emboss); }
  .card--brand .brand__main { font-size: 118px; }
  .card--brand .brand__sub { font-size: 25px; margin-top: 8px; }
</style>
</head>
<body>
<main class="canvas">

  <section class="card card--contact" aria-label="Contact side">
    <div class="brand">
      <span class="brand__main">VOR</span>
      <span class="brand__sub">Exterior Coatings</span>
    </div>
    <div class="divider"></div>
    <div class="contact">
      <p class="contact__name">Daniel Brooks</p>
      <p class="contact__title">Founder &amp; CEO</p>
      <p class="contact__address">4210 Cedar Ridge Road<br>Anchorage, Alaska 99501</p>
      <ul class="contact__list">
        <li>
          <svg viewBox="0 0 12 12" aria-hidden="true"><path class="icon" d="M2.5 0.8l2 2-1 1.4c.6 1.5 1.8 2.7 3.3 3.3l1.4-1 2 2-1.2 1.8C5 10.3 1.7 7 .7 2z"/></svg>
          555-214-7830
        </li>
        <li>
          <svg viewBox="0 0 12 12" aria-hidden="true"><path class="icon" d="M3 0h6v12H3zM4 1.5v8h4v-8z"/></svg>
          555-362-9147
        </li>
        <li>
          <svg viewBox="0 0 12 12" aria-hidden="true"><path class="icon" d="M3 0h6v4H3zM1 4.5h10V10H1zM3 10.5h6V12H3z"/></svg>
          555-781-4026
        </li>
        <li>
          <svg viewBox="0 0 12 12" aria-hidden="true"><path class="icon" d="M0 2h12v8H0zM1 3l5 3.5L11 3v-.2H1z"/></svg>
          info@vorexteriorcoatings.com
        </li>
        <li>
          <svg viewBox="0 0 12 12" aria-hidden="true"><circle class="icon" cx="6" cy="6" r="6"/><path d="M0 6h12M6 0c-3 3-3 9 0 12M6 0c3 3 3 9 0 12" stroke="#f6f6f5" stroke-width="0.8" fill="none"/></svg>
          www.vorexteriorcoatings.com
        </li>
      </ul>
    </div>
  </section>

  <section class="card card--brand" aria-label="Brand side">
    <div class="brand">
      <span class="brand__main">VOR</span>
      <span class="brand__sub">Exterior Coatings</span>
    </div>
  </section>

</main>
</body>
</html>
```